Home Page for a Swiss based start up company, trading Natural & Health food ingredients (B2B)

I would like to create a home page for my new start up company (Veltrana Swiss AG), the main field of activity is the trading and marketing of Natural and Health food ingredients towards the functional Food and Food supplements industry. (B2B).
Target Market : Functional Food and Food Supplement Manufacturers (B2B) based in Switzerland and Europe
The values I would like to convey are :
- sourcing of natural and health ingredients, (example : natural plant extracts, Omega 3, plant proteins, natural vitamins, vegan food ingredients...etc)
- Health & Nutritional Health
- Eco-friendly and Sustainability
- High Quality Standard in term of products and logistic services
- Trust and reliability
- Flexibility & speed to market
-Technical advice for the development of new products

The site will be translated in 3 languages (German, French, English)
Number of web pages : 5 : Home, About us, Products, Our Services, Contact

See here below attached Logo file.

Here some link of websites which can be taken as benchmark or source of inspiration
- https://quorbelix.com
- https://www.dralvimo.com/

Target Market(s)

Manufacturers of Functional Foods and Food Supplements in Switzerland and Europe (B2B)

Industry/Entity Type

B2B Trading of Natural & Health Ingredients

Coding

Number of Pages Required

Font styles to use
Sans Serif

Colors
0054AA
0677BA
7BADD7
CADEEF
E8F1F8
0094D4
00A9DD
6FCCEA
C7EBF8
E9F6FB
00AB8E
00BBA5
67D7C9
C6EFE9
E9F9F6
59FF00
82FF00
B8FF75
E3FFCB
F4FFEA
FFF300
FFF600
FEFA6F
FFFEC7
FFFEE8
FFC000
F8CF3A
FAE287
FDF2CF
FEFAEE
F0912C
F2A743
F7CA91
FBE8D2
FDF5EE
EE7325
F08F49
F5BC92
FAE3D3
FDF4ED

Requirements
Must have
• inspiration towards nature, sustainability, vegan food, functional food & beverages, food supplements, nutritional health, low carbon footprint
Should not have
• animals, chemistry, food additives

```html
<!DOCTYPE html>
<html lang="en">
<head>
<meta charset="utf-8">
<title>Veltrana Swiss AG – Natural &amp; Health Food Ingredients</title>
<link rel="stylesheet" href="https://fonts.googleapis.com/css2?family=Montserrat:wght@400;500;600;700;800&family=Open+Sans:wght@400;600&display=swap">
<style>
:root{
  --orange:#EE7325;
  --orange-soft:#F08F49;
  --green:#00AB8E;
  --green-soft:#00BBA5;
  --ink:#2b2b2b;
  --muted:#6d6d6d;
  --white:#ffffff;
  --footer:#1f1f1f;
  --line:#e6e6e6;
}
*{box-sizing:border-box;margin:0;padding:0}
html,body{width:1200px;height:3648px;overflow:hidden}
body{font-family:"Open Sans",Arial,sans-serif;color:var(--ink);background:var(--white);position:relative}
h1,h2,h3,.nav,.btn,.brand{font-family:"Montserrat",Arial,sans-serif}
section,header,footer{position:absolute;left:0;width:1200px}

/* hero */
.hero{top:0;height:780px;background:linear-gradient(180deg,#e4e4e2 0%,#d6d6d3 38%,#c9b89a 55%,#9bb07a 72%,#c98b4f 100%)}
.hero-photo{position:absolute;left:0;top:330px;width:1200px;height:450px;background:linear-gradient(100deg,#8fa85c 0%,#c4513a 25%,#6e8f3e 45%,#e0a53c 65%,#5a7f35 82%,#b9743d 100%);opacity:.55}
.nav{position:absolute;left:110px;top:44px;width:980px;height:76px;background:var(--white);border-radius:38px;display:flex;align-items:center;padding:0 36px;box-shadow:0 4px 14px rgba(0,0,0,.08)}
.nav .brand{font-size:30px;font-weight:800;color:var(--orange);letter-spacing:.5px}
.nav ul{list-style:none;display:flex;gap:30px;margin-left:auto;font-size:15px;font-weight:600;color:var(--ink)}
.nav li.active{color:var(--orange)}
.nav .lang{margin-left:28px;background:var(--orange);color:var(--white);font-size:14px;font-weight:700;padding:6px 14px;border-radius:16px}
.hero h1{position:absolute;top:200px;width:100%;text-align:center;font-size:84px;font-weight:500;color:var(--ink);letter-spacing:2px}
.hero .tagline{position:absolute;top:296px;width:100%;text-align:center;font-family:"Montserrat",Arial,sans-serif;font-size:22px;font-weight:700;color:var(--ink);letter-spacing:1px}

/* trading / marketing */
.pillars{top:780px;height:160px;display:flex}
.pillar{width:600px;height:160px;display:flex;align-items:center;padding-left:70px;gap:26px;color:var(--white)}
.pillar.trading{background:var(--green)}
.pillar.marketing{background:var(--orange)}
.pillar .icon{width:90px;height:90px;border-radius:50%;background:var(--white);display:flex;align-items:center;justify-content:center;flex:none}
.pillar h3{font-size:30px;font-weight:700;letter-spacing:1px;margin-bottom:8px}
.pillar p{font-size:14px;line-height:1.5;width:360px}

/* welcome */
.welcome{top:960px;height:540px}
.welcome-photo{position:absolute;left:110px;top:40px;width:460px;height:440px;border-radius:50% 50% 48% 48%;background:radial-gradient(circle at 40% 45%,#e67b55 0%,#b9d08a 40%,#7ea24d 70%,#ffffff 71%)}
.welcome-body{position:absolute;left:680px;top:60px;width:420px}
.welcome-body .kicker{font-family:"Montserrat",Arial,sans-serif;font-size:18px;font-weight:700;color:var(--ink)}
.welcome-body h2{font-size:46px;font-weight:700;color:var(--orange);margin:4px 0 22px}
.welcome-body p{font-size:14px;line-height:1.75;color:var(--muted)}
.btn{display:inline-block;margin-top:28px;padding:14px 30px;border-radius:28px;font-size:14px;font-weight:700;color:var(--white);letter-spacing:.5px}
.btn.green{background:var(--green)}
.btn.orange{background:var(--orange)}

/* core values */
.values{top:1520px;height:660px;background:linear-gradient(135deg,var(--orange) 0%,#ea6a1d 100%)}
.values h2{position:absolute;top:48px;width:100%;text-align:center;font-size:44px;font-weight:700;color:var(--white);letter-spacing:1px}
.values .rule{position:absolute;top:112px;left:560px;width:80px;height:3px;background:var(--white)}
.value{position:absolute;width:480px;height:100px;background:var(--white);border-radius:50px;display:flex;align-items:center;font-size:16px;font-weight:600;color:var(--ink);line-height:1.35}
.value.left{left:110px;justify-content:flex-end;padding-right:14px;text-align:right}
.value.right{left:610px;padding-left:14px}
.value .label{width:300px}
.value.left .label{margin-right:22px}
.value.right .label{margin-left:22px}
.badge{width:78px;height:78px;border-radius:50%;display:flex;align-items:center;justify-content:center;flex:none;border:3px solid}
.badge.o{border-color:var(--orange)}
.badge.g{border-color:var(--green)}

/* why choose us */
.why{top:2190px;height:540px}
.why-photo{position:absolute;left:0;top:0;width:600px;height:540px;background:linear-gradient(160deg,#e9ece3 0%,#cfd7bf 45%,#a7bd7a 75%,#8a6a4a 100%)}
.why-body{position:absolute;left:630px;top:130px;width:470px}
.why-body h2{font-size:44px;font-weight:700;color:var(--orange);margin-bottom:20px}
.why-body p{font-size:14px;line-height:1.75;color:var(--muted)}
.why-body ul{list-style:none;margin-top:16px}
.why-body li{font-size:14px;color:var(--muted);line-height:2.1;display:flex;align-items:center;gap:12px}
.why-body li::before{content:"";width:9px;height:9px;border-radius:50%;background:var(--orange);flex:none}

/* blog */
.blog{top:2760px;height:560px}
.blog h2{position:absolute;top:10px;width:100%;text-align:center;font-size:44px;font-weight:700;color:var(--orange)}
.blog .rule{position:absolute;top:72px;left:560px;width:80px;height:3px;background:var(--green)}
.post{position:absolute;top:110px;width:480px;height:420px;background:var(--white);box-shadow:0 4px 16px rgba(0,0,0,.08)}
.post.one{left:110px}
.post.two{left:610px}
.post-photo{width:480px;height:260px}
.post.one .post-photo{background:linear-gradient(135deg,#f2efe9 0%,#ded4c0 55%,#b79a6e 100%)}
.post.two .post-photo{background:linear-gradient(135deg,#7d8a4a 0%,#c79a52 45%,#8e5b39 100%)}
.date{position:absolute;right:24px;top:210px;width:92px;height:92px;border-radius:50%;background:var(--orange);color:var(--white);text-align:center;font-family:"Montserrat",Arial,sans-serif;border:5px solid var(--white)}
.date b{display:block;font-size:28px;font-weight:700;margin-top:14px;line-height:1}
.date span{font-size:13px;font-weight:600}
.meta{display:flex;gap:24px;font-size:13px;color:var(--muted);padding:26px 24px 10px}
.meta span{display:flex;align-items:center;gap:6px}
.post h3{font-family:"Open Sans",Arial,sans-serif;font-size:17px;font-weight:600;line-height:1.5;padding:0 24px;color:var(--ink)}

/* footer */
.site-footer{top:3340px;height:308px;background:var(--footer);color:var(--white);text-align:center}
.site-footer .brand{display:block;margin-top:52px;font-size:46px;font-weight:700;color:var(--white);letter-spacing:1px}
.site-footer ul{list-style:none;display:flex;justify-content:center;gap:34px;margin-top:28px;font-family:"Montserrat",Arial,sans-serif;font-size:14px;font-weight:600}
.social{display:flex;justify-content:center;gap:14px;margin-top:28px}
.social span{width:38px;height:38px;border-radius:50%;border:2px solid var(--white)}
.copy{margin-top:26px;font-size:13px;color:#cfcfcf}
</style>
</head>
<body>

<header class="hero">
  <div class="hero-photo" role="img" aria-label="Overhead spread of fresh vegetables, fruits, grains, seeds and nuts in bowls on stone"></div>
  <nav class="nav">
    <span class="brand">VELTRANA SWISS</span>
    <ul>
      <li class="active">HOME</li>
      <li>ABOUT US</li>
      <li>SERVICES</li>
      <li>VALUES</li>
      <li>NEWS</li>
      <li>CONTACT US</li>
    </ul>
    <span class="lang">EN ▾</span>
  </nav>
  <h1>VELTRANA SWISS</h1>
  <p class="tagline">SED UT PERSPICIATIS UNDE OMNIS ISTE NATUS ERROR SIT</p>
</header>

<section class="pillars">
  <div class="pillar trading">
    <div class="icon">
      <svg width="46" height="46" viewBox="0 0 46 46" fill="none" stroke="#00AB8E" stroke-width="3" stroke-linecap="round" stroke-linejoin="round"><path d="M6 40h34"/><path d="M10 34V26M18 34V20M26 34V24M34 34V14"/><path d="M8 20l10-8 8 6 12-10"/></svg>
    </div>
    <div>
      <h3>TRADING</h3>
      <p>Sed ut perspiciatis unde omnis iste natus error sit voluptatem accusantium doloremque laudantium.</p>
    </div>
  </div>
  <div class="pillar marketing">
    <div class="icon">
      <svg width="46" height="46" viewBox="0 0 46 46" fill="none" stroke="#EE7325" stroke-width="3" stroke-linecap="round" stroke-linejoin="round"><path d="M8 18h8l16-9v28l-16-9H8z"/><path d="M14 28l3 10h5l-2-10"/><path d="M37 17c2 2 2 10 0 12"/></svg>
    </div>
    <div>
      <h3>MARKETING</h3>
      <p>Sed ut perspiciatis unde omnis iste natus error sit voluptatem accusantium doloremque laudantium.</p>
    </div>
  </div>
</section>

<section class="welcome">
  <div class="welcome-photo" role="img" aria-label="Heart-shaped arrangement of salmon, avocado, vegetables, nuts and grains"></div>
  <div class="welcome-body">
    <p class="kicker">WELCOME TO</p>
    <h2>VELTRANA SWISS</h2>
    <p>Sed ut perspiciatis unde omnis iste natus error sit voluptatem accusantium doloremque laudantium, totam rem aperiam, eaque ipsa quae ab illo inventore veritatis et quasi architecto beatae vitae dicta sunt explicabo. Nemo enim ipsam voluptatem quia voluptas sit aspernatur aut odit aut fugit, sed quia consequuntur magni dolores eos qui ratione voluptatem sequi nesciunt. Neque porro quisquam est, qui dolorem ipsum quia dolor sit amet, consectetur.</p>
    <span class="btn green">READ MORE</span>
  </div>
</section>

<section class="values">
  <h2>CORE VALUES</h2>
  <div class="rule"></div>

  <div class="value left" style="top:160px"><span class="label">Sourcing of natural and health ingredients</span>
    <span class="badge o"><svg width="40" height="40" viewBox="0 0 40 40" fill="none" stroke="#EE7325" stroke-width="2.5" stroke-linecap="round" stroke-linejoin="round"><path d="M20 8c-8 0-12 6-12 13s5 13 12 13 12-6 12-13S28 8 20 8z"/><path d="M20 8c0-3 2-5 5-5"/></svg></span></div>
  <div class="value right" style="top:160px"><span class="badge o"><svg width="40" height="40" viewBox="0 0 40 40" fill="none" stroke="#EE7325" stroke-width="2.5" stroke-linecap="round" stroke-linejoin="round"><rect x="9" y="7" width="22" height="27" rx="2"/><path d="M14 21l4 4 8-8"/></svg></span><span class="label">Trust and reliability</span></div>

  <div class="value left" style="top:280px"><span class="label">Health &amp; Nutritional Health</span>
    <span class="badge g"><svg width="40" height="40" viewBox="0 0 40 40" fill="none" stroke="#00AB8E" stroke-width="2.5" stroke-linecap="round" stroke-linejoin="round"><path d="M20 33S6 24 6 15a7 7 0 0 1 14-2 7 7 0 0 1 14 2c0 9-14 18-14 18z"/><path d="M11 19h5l2-4 4 8 2-4h5"/></svg></span></div>
  <div class="value right" style="top:280px"><span class="badge g"><svg width="40" height="40" viewBox="0 0 40 40" fill="none" stroke="#00AB8E" stroke-width="2.5" stroke-linecap="round" stroke-linejoin="round"><circle cx="20" cy="21" r="13"/><path d="M20 13v8l6 4"/></svg></span><span class="label">Flexibility &amp; speed to market</span></div>

  <div class="value left" style="top:400px"><span class="label">Eco-friendly and Sustainability</span>
    <span class="badge o"><svg width="40" height="40" viewBox="0 0 40 40" fill="none" stroke="#EE7325" stroke-width="2.5" stroke-linecap="round" stroke-linejoin="round"><path d="M10 30C10 16 20 8 32 8c0 14-8 22-20 22"/><path d="M10 30l12-12"/></svg></span></div>
  <div class="value right" style="top:400px"><span class="badge o"><svg width="40" height="40" viewBox="0 0 40 40" fill="none" stroke="#EE7325" stroke-width="2.5" stroke-linecap="round" stroke-linejoin="round"><rect x="7" y="9" width="26" height="20" rx="2"/><path d="M14 34h12M20 29v5"/><circle cx="20" cy="19" r="4"/></svg></span><span class="label">Technical advice for the development of new products</span></div>

  <div class="value left" style="top:520px"><span class="label">High Quality Standard in term of products and logistic services</span>
    <span class="badge g"><svg width="40" height="40" viewBox="0 0 40 40" fill="none" stroke="#00AB8E" stroke-width="2.5" stroke-linecap="round" stroke-linejoin="round"><circle cx="20" cy="16" r="9"/><path d="M14 23l-3 11 9-4 9 4-3-11"/></svg></span></div>
  <div class="value right" style="top:520px"><span class="badge g"><svg width="40" height="40" viewBox="0 0 40 40" fill="none" stroke="#00AB8E" stroke-width="2.5" stroke-linecap="round" stroke-linejoin="round"><path d="M20 5l12 5v9c0 8-5 13-12 16-7-3-12-8-12-16v-9z"/><path d="M14 20l4 4 8-8"/></svg></span><span class="label">Security of supply</span></div>
</section>

<section class="why">
  <div class="why-photo" role="img" aria-label="Smiling woman at a kitchen table with a fresh salad, juices and vegetables"></div>
  <div class="why-body">
    <h2>WHY CHOOSE US</h2>
    <p>Sed ut perspiciatis unde omnis iste natus error sit voluptatem accusantium doloremque laudantium, totam rem aperiam, eaque ipsa quae ab illo inventore veritatis et quasi architecto.</p>
    <ul>
      <li>Sed ut perspiciatis unde omnis iste natus</li>
      <li>error sit voluptatem accusantium</li>
      <li>doloremque laudantium, totam rem aperiam</li>
      <li>eaque ipsa quae ab illo inventore veritatis</li>
      <li>beatae vitae dicta sunt explicabo</li>
    </ul>
    <span class="btn orange">READ MORE</span>
  </div>
</section>

<section class="blog">
  <h2>LATEST BLOG</h2>
  <div class="rule"></div>
  <article class="post one">
    <div class="post-photo" role="img" aria-label="Plant protein powder in a jar with a scoop and capsules"></div>
    <div class="date"><b>27</b><span>APR</span></div>
    <div class="meta"><span>👤 by admin</span><span>💬 Comment (5)</span></div>
    <h3>Sed ut perspiciatis unde omnis iste natus error sit voluptatem accusantium dolorem</h3>
  </article>
  <article class="post two">
    <div class="post-photo" role="img" aria-label="Bowls of natural supplements, seeds and dried herbs"></div>
    <div class="date"><b>27</b><span>APR</span></div>
    <div class="meta"><span>👤 by admin</span><span>💬 Comment (5)</span></div>
    <h3>Sed ut perspiciatis unde omnis iste natus error sit voluptatem accusantium dolorem</h3>
  </article>
</section>

<footer class="site-footer">
  <span class="brand">VELTRANA SWISS</span>
  <ul>
    <li>HOME</li>
    <li>ABOUT US</li>
    <li>SERVICES</li>
    <li>VALUES</li>
    <li>NEWS</li>
    <li>CONTACT US</li>
  </ul>
  <div class="social" aria-label="Social links"><span></span><span></span><span></span><span></span></div>
  <p class="copy">© Copyright 2022 Veltrana Swiss. All Rights Reserved</p>
</footer>

</body>
</html>
```